Redesign This Psychology Website

We would like a slight redesign of this successful psychology (relationship counselling) website:

www.TheKelvaleClinic.com.au

We are updating the website, and we'd like a slight refresh of the design and style.

Please keep to very similar colours, and use the same logo. We're looking for around 10 page templates, however the main one is the home page.

Keep in mind, this website already converts quite well, so we want a new, fresh design in keeping with this one. Please don't bother designing something too extremely different.

thanks :)

Target Market(s)

couples who are looking for relationship counselling. Men and women, 25 - 70, across Australia

Industry/Entity Type

Psychology

Number of Pages Required

5+ page

Font styles to use
Sans Serif

Colors
87cfc6
b7a5cd
ec1f27
ffffff
cee9f5

Requirements
Must have
• a similar look to the current design, just looking for a slight refresh.
• Search bar
• Areas for lots of photos
• same logo
• lots of content areas
Nice to have
• great content areas, where we can display a lot of content and our areas.
Should not have
• no colors like orange, etc.
• should not have a totally different feel.

```html
<!DOCTYPE html>
<html lang="en">
<head>
<meta charset="utf-8">
<title>The Kelvale Clinic – Relationship Counselling</title>
<link href="https://fonts.googleapis.com/css2?family=Lato:ital,wght@0,300;0,400;0,700;1,400;1,700&display=swap" rel="stylesheet">
<style>
:root{
  --teal:#2a9d9b;
  --teal-dark:#1f8482;
  --teal-head:#19888a;
  --teal-card:#5bbcb5;
  --teal-light:#87cfc6;
  --red:#e52b3a;
  --grey-bg:#f1f2f2;
  --text:#555;
  --line:#d9dcdc;
  --white:#fff;
}
*{box-sizing:border-box;margin:0;padding:0}
html,body{width:1200px;height:4337px;overflow:hidden;background:var(--white)}
body{font-family:'Lato',sans-serif;color:var(--text);position:relative}
.abs{position:absolute}
a{color:inherit;text-decoration:none}
.ph{position:absolute;overflow:hidden}
.btn{position:absolute;background:var(--teal-dark);color:#fff;font-size:16px;letter-spacing:.5px;padding:0 30px;height:42px;line-height:42px;text-transform:uppercase}
h2.sec{position:absolute;font-weight:400;color:var(--teal-head);font-size:36px;line-height:1.15}
h2.sec em{font-style:normal;color:var(--red)}
p.body{position:absolute;font-size:14px;line-height:1.6;color:#666}

/* top bar */
.topbar{top:0;left:0;width:1200px;height:46px;background:var(--teal)}
.topbar .soc{top:15px;width:16px;height:16px;border-radius:50%;background:#fff}
.toplinks{top:0;left:408px;height:46px;display:flex}
.toplinks a{color:#fff;font-size:14px;line-height:46px;padding:0 14px;border-left:1px solid rgba(255,255,255,.4)}
.toplinks a.on{background:var(--teal-dark)}

/* header */
.logo{top:62px;left:78px;display:flex;align-items:center;gap:14px}
.logo .dot{width:56px;height:56px;border-radius:50%;background:var(--red)}
.logo .name{font-size:38px;font-weight:700;color:var(--teal-head);line-height:1}
.tagline{top:110px;left:148px;font-size:14px;color:var(--teal-head)}
.search{top:72px;left:717px;width:405px;height:55px;border:1px solid #ccc;background:#f7f7f7;font-size:16px;line-height:53px;padding-left:16px;color:#333}
.search svg{position:absolute;right:16px;top:16px}

/* nav */
.nav{top:159px;left:78px;width:1044px;height:78px;border-top:1px solid var(--line);border-bottom:1px solid var(--line);display:flex}
.nav .home{width:96px;flex:none;background:var(--teal);display:flex;align-items:center;justify-content:center}
.nav a{flex:1;text-align:center;line-height:76px;font-size:14px;color:#777;border-left:1px solid var(--line);text-transform:uppercase;white-space:nowrap}

/* hero */
.hero{top:237px;left:0;width:1200px;height:573px;
  background:
   radial-gradient(ellipse 300px 170px at 400px 390px,rgba(90,110,130,.55),transparent 70%),
   radial-gradient(ellipse 220px 160px at 280px 300px,rgba(230,200,180,.55),transparent 70%),
   repeating-linear-gradient(90deg,rgba(0,0,0,.06) 0 2px,transparent 2px 140px),
   linear-gradient(180deg,#f6f3ee 0%,#ece6dc 52%,#c59a68 62%,#a7743f 80%,#7c522b 100%);}
.hero-title{top:304px;left:640px;width:500px;font-size:31px;font-weight:700;color:var(--teal-head);line-height:1.2;text-align:right}
.hero-frame{top:405px;left:688px;width:434px;height:237px;background:linear-gradient(180deg,#fdfdfd,#e6e6e6);box-shadow:0 6px 14px rgba(0,0,0,.25);display:flex;align-items:center;justify-content:center;gap:10px}
.hero-frame .dot{width:34px;height:34px;border-radius:50%;background:var(--red)}
.hero-frame .name{font-size:26px;font-weight:700;color:var(--teal-head)}

/* service cards */
.cards{top:804px;left:78px;width:1044px;height:367px;display:flex;gap:6px}
.card{flex:1;background:var(--teal-card);position:relative;color:#fff;border-top:4px solid var(--teal-light);overflow:hidden}
.card h3{position:absolute;top:38px;left:14px;right:10px;font-size:18px;font-weight:400;line-height:1.15}
.card .need{position:absolute;top:84px;left:14px;font-size:13px;font-weight:700}
.card .list{position:absolute;top:106px;left:14px;right:14px;font-size:13px;line-height:1.25}
.card .cta{position:absolute;top:185px;left:14px;width:96px;font-size:13px;font-style:italic;font-weight:700;line-height:1.2;z-index:1}
.card .more{position:absolute;bottom:16px;left:14px;font-size:15px;text-decoration:underline;color:#123;z-index:1}
.card .photo{position:absolute;right:0;bottom:0;width:150px;height:200px}

/* find */
.find-sec{top:1171px;left:0;width:1200px;height:521px;background:var(--grey-bg)}
.find{top:1229px;left:0;width:477px;height:405px;background:#fff;box-shadow:0 4px 14px rgba(0,0,0,.2)}
.find h2{position:absolute;top:36px;left:14px;font-size:31px;font-weight:400;color:var(--teal-head)}
.find h2 em{font-style:normal;color:var(--red)}
.find .inner{position:absolute;top:100px;left:20px;width:435px;height:262px;background:#e9ecec;border:1px solid #d4d8d8}
.frow{position:absolute;left:0;width:200px;text-align:right;font-size:17px;color:#555}
.fin{position:absolute;left:232px;width:182px;height:38px;background:#fff;border:1px solid #c7cccc;font-size:13px;line-height:36px;padding-left:8px}
.find .btn{left:254px;top:300px;width:184px;text-align:center;padding:0;height:44px;line-height:44px}

/* psychologists */
.ad{top:1755px;left:818px;width:304px;height:240px;background:radial-gradient(ellipse 120px 150px at 230px 100px,#e6b9a3,transparent 70%),linear-gradient(90deg,#f6f6f6 0%,#f1ddd5 55%,#c98f76 100%)}
.ad .q{position:absolute;top:8px;left:10px;font-size:25px;font-weight:700;font-style:italic;color:var(--red);line-height:1.15}
.ad .band{position:absolute;left:0;right:0;bottom:0;height:50px;background:var(--red);color:#fff;font-size:14px;line-height:1.2;padding:6px 10px}
.dots{top:2006px;left:957px;display:flex;gap:5px}
.dots i{width:14px;height:14px;border-radius:50%;border:2px solid #888;display:block}
.dots i.on{background:#555}

/* locations */
.loc-sec{top:2082px;left:0;width:1200px;height:376px;background:var(--grey-bg)}
.loc-grid{top:2262px;left:100px;width:1020px;display:grid;grid-template-columns:270px 240px 232px 270px;row-gap:10px;font-size:15px;color:#555}
.loc-grid span{display:flex;align-items:center;gap:8px;white-space:nowrap}
.loc-grid b{color:#222}
.loc-grid svg{flex:none}

/* photos */
.ph-approach{top:2501px;left:78px;width:521px;height:362px;box-shadow:0 6px 14px rgba(0,0,0,.25);
  background:radial-gradient(ellipse 110px 150px at 150px 230px,#d66a55,transparent 70%),
   radial-gradient(ellipse 120px 160px at 290px 200px,#e8d2c4,transparent 70%),
   radial-gradient(ellipse 110px 150px at 440px 250px,#9fb8c8,transparent 70%),
   linear-gradient(180deg,#f4f5f3 0%,#e4e7e3 60%,#c8c4bb 100%)}
.ph-couple{top:2921px;left:714px;width:408px;height:405px;
  background:radial-gradient(ellipse 150px 190px at 230px 230px,#3e3a3a,transparent 72%),
   radial-gradient(ellipse 90px 110px at 170px 180px,#d9a983,transparent 70%),
   repeating-linear-gradient(0deg,rgba(0,0,0,.08) 0 3px,transparent 3px 48px),
   linear-gradient(135deg,#d2b48f,#a98562 55%,#6f5540)}

/* faq */
.faq-item{position:absolute;left:78px;width:636px;font-size:15px;color:#2a5f7a;border-bottom:2px solid var(--teal-light);padding:8px 0 10px 22px}
.faq-item::before{content:"+";position:absolute;left:0;top:3px;color:var(--red);font-size:22px;font-weight:700}
.faq-item.open::before{content:"–"}
.faq-vline{top:3515px;left:740px;width:1px;height:235px;background:var(--line)}

/* blogs */
.blog-sec{top:3817px;left:0;width:1200px;height:362px;background:var(--grey-bg)}
.blog{position:absolute;top:3939px;width:312px;height:182px;box-shadow:0 3px 10px rgba(0,0,0,.25);overflow:hidden}
.blog .date{position:absolute;left:20px;bottom:42px;font-size:12px;color:#fff}
.blog .t{position:absolute;left:0;right:0;bottom:0;height:36px;background:rgba(0,0,0,.55);color:#fff;font-size:14px;font-weight:700;line-height:36px;padding-left:20px}
.b1{background:radial-gradient(ellipse 90px 90px at 200px 70px,#c9a58b,transparent 70%),linear-gradient(135deg,#7b8a8e,#3c4548)}
.b2{background:radial-gradient(ellipse 110px 80px at 120px 80px,#efe7df,transparent 70%),linear-gradient(135deg,#b9b2aa,#5f5a55)}
.b3{background:radial-gradient(ellipse 100px 90px at 180px 70px,#b97a5a,transparent 70%),linear-gradient(135deg,#8a6a4f,#3f3128)}

/* footer */
.footer{top:4179px;left:0;width:1200px;height:95px;background:linear-gradient(180deg,var(--teal-light),var(--teal))}
.flinks{top:4216px;left:0;width:1200px;display:flex;justify-content:center;font-size:14px;color:#1d3e45}
.flinks a{padding:0 16px;border-left:1px solid #1d3e45}
.flinks a:first-child{border-left:0}
.fbottom{top:4274px;left:0;width:1200px;height:63px;background:var(--teal-dark);color:#fff;font-size:14px}
.fbottom .c{position:absolute;left:78px;top:22px}
.fbottom .s{position:absolute;top:20px;width:22px;height:22px;background:#fff}
</style>
</head>
<body>

<div class="abs topbar">
  <span class="abs soc" style="left:78px"></span>
  <span class="abs soc" style="left:104px"></span>
  <span class="abs soc" style="left:130px"></span>
  <nav class="abs toplinks">
    <a href="#">JOIN OUR ASSOCIATION PROGRAM</a>
    <a href="#">MARRIAGE COUNSELLING</a>
    <a href="#" class="on">RELATIONSHIP COUNSELLING</a>
  </nav>
</div>

<div class="abs logo"><span class="dot"></span><span class="name">The Kelvale Clinic</span></div>
<div class="abs tagline">helping you create loving relationships</div>
<div class="abs search">Search
  <svg width="22" height="22" viewBox="0 0 22 22"><circle cx="9" cy="9" r="6.5" fill="none" stroke="#e52b3a" stroke-width="2.5"/><line x1="14" y1="14" x2="20" y2="20" stroke="#e52b3a" stroke-width="3"/></svg>
</div>

<nav class="abs nav">
  <span class="home"><svg width="30" height="28" viewBox="0 0 30 28"><path d="M15 2 L28 14 H24 V26 H18 V18 H12 V26 H6 V14 H2 Z" fill="#fff"/></svg></span>
  <a href="#">About us</a><a href="#">Resources</a><a href="#">Counselling</a><a href="#">Location</a><a href="#">Quizzes</a><a href="#">FAQ</a><a href="#">Blog</a><a href="#">Store</a><a href="#">Contact us</a>
</nav>

<div class="ph hero" role="img" aria-label="Photo of a smiling couple sitting together on a wooden floor"></div>
<h1 class="abs hero-title">We Specialise in Relationship &amp; Marriage Counselling</h1>
<div class="ph hero-frame"><span class="dot"></span><span class="name">The Kelvale Clinic</span></div>

<div class="abs cards">
  <div class="card">
    <div class="photo" role="img" aria-label="Photo of a smiling man" style="background:radial-gradient(ellipse 60px 80px at 80px 110px,#f2f0ea,transparent 72%),radial-gradient(ellipse 40px 40px at 82px 50px,#e3b99a,transparent 72%),linear-gradient(180deg,#5bbcb5,#4aa7a1)"></div>
    <h3>Relationship Counselling</h3>
    <div class="need">Do you need help with</div>
    <div class="list">Communication, Recovering from an affair, Loss of intimacy &amp; love, Power battles, Feeling like friends, not lovers.</div>
    <div class="cta">Take our Relationship Quiz</div>
    <a class="more" href="#">Read More</a>
  </div>
  <div class="card">
    <div class="photo" role="img" aria-label="Photo of a couple relaxing together" style="background:radial-gradient(ellipse 70px 70px at 70px 120px,#f7f5f2,transparent 72%),radial-gradient(ellipse 50px 40px at 100px 70px,#c98a6a,transparent 72%),linear-gradient(180deg,#5bbcb5,#4aa7a1)"></div>
    <h3>Sex Therapy Counselling</h3>
    <div class="need">Do you need help with</div>
    <div class="list">Communication, Recovering from an affair, Loss of intimacy &amp; love, Power battles, Feeling like friends, not lovers.</div>
    <div class="cta">Take our Sex Quiz</div>
    <a class="more" href="#">Read More</a>
  </div>
  <div class="card">
    <div class="photo" role="img" aria-label="Photo of a man in a suit" style="background:radial-gradient(ellipse 65px 100px at 80px 150px,#2d3438,transparent 72%),radial-gradient(ellipse 35px 40px at 80px 55px,#d9ad90,transparent 72%),linear-gradient(180deg,#5bbcb5,#4aa7a1)"></div>
    <h3 style="top:28px">Anger Management Counselling</h3>
    <div class="need">Do you need help with</div>
    <div class="list">Communication, Recovering from an affair, Loss of intimacy &amp; love, Power battles, Feeling like friends, not lovers.</div>
    <div class="cta">Take our Anger Test</div>
    <a class="more" href="#">Read More</a>
  </div>
  <div class="card">
    <div class="photo" role="img" aria-label="Photo of a person in a dark jacket" style="background:radial-gradient(ellipse 65px 100px at 90px 150px,#2a2d30,transparent 72%),radial-gradient(ellipse 35px 40px at 90px 55px,#d3a88c,transparent 72%),linear-gradient(180deg,#5bbcb5,#4aa7a1)"></div>
    <h3>Narcissism Counselling</h3>
    <div class="need">Do you need help with</div>
    <div class="list">Communication, Recovering from an affair, Loss of intimacy &amp; love, Power battles, Feeling like friends, not lovers.</div>
    <div class="cta">Check your Narcissism Profile</div>
    <a class="more" href="#">Read More</a>
  </div>
</div>

<div class="abs find-sec"></div>
<div class="abs find">
  <h2>Find Our Psychologist <em>Near You</em></h2>
  <div class="inner">
    <div class="frow" style="top:30px">Type of Counselling :</div>
    <div class="fin" style="top:24px">Select...</div>
    <div class="frow" style="top:88px">Location :</div>
    <div class="fin" style="top:82px"></div>
    <div class="frow" style="top:122px;width:300px;text-align:center">OR</div>
    <div class="frow" style="top:152px">Postal Code :</div>
    <div class="fin" style="top:146px"></div>
  </div>
  <a class="btn" href="#">Search</a>
</div>
<h2 class="sec" style="top:1232px;left:529px;width:560px">We Specialise in Relationship &amp; Marriage Counselling</h2>
<p class="body" style="top:1335px;left:529px;width:590px">At The Kelvale Clinic, we are a group of PSYCHOLOGISTS, Australia wide who are passionate about relationships and helping you with yours.<br><br>Our vision is to provide the most highly regarded and comprehensive marriage counselling and relationship counselling, and sex therapy in Australia, at reasonable and affordable rates.<br><br>When we are experiencing relationship and marriage problems, there can be a lot of pain and confusion, and it can often be difficult to cope with the other areas of our lives when we are struggling with problems with our partner.</p>
<a class="btn" href="#" style="top:1563px;left:529px">Read More</a>

<h2 class="sec" style="top:1738px;left:78px">Our Kelvale Relationship <em>Psychologists</em></h2>
<p class="body" style="top:1795px;left:78px;width:660px">Our team of 75 hand chosen Registered Psychologists in 85 locations Australia wide, are individually selected for their knowledge, experience, compassion, and unbiased approach to marriage counselling and sexual therapy.<br><br>In addition all our Psychologists take part in our Initial Relationship Counselling Methodologies Training and yearly In-house conferences, ensuring you are in safe and experienced hands.<br><br>As we are Psychologists, you may be eligible for Medicare &amp; Private Health Insurance Rebates.</p>
<a class="btn" href="#" style="top:1985px;left:78px">Read More</a>
<div class="ph ad" role="img" aria-label="Promotional photo of a worried woman">
  <div class="q">Is Anxiety,<br>Depression<br>or Stress<br>bothering<br>YOU?</div>
  <div class="band">Click here for <b>help</b> from Kelvale Anxiety &amp; Depression Psychologists</div>
</div>
<div class="abs dots"><i class="on"></i><i></i><i></i></div>

<div class="abs loc-sec"></div>
<h2 class="sec" style="top:2126px;left:0;width:1200px;text-align:center;font-size:32px">Our Relationship Counselling Locations <em>across Australia</em></h2>
<p class="body" style="top:2180px;left:250px;width:700px;text-align:center">Certain clinics also provide after hours and Saturday sessions for your convenience. Click the Locations tab for more information about one of our caring psychologists in your area.</p>
<div class="abs loc-grid">
  <span><svg width="14" height="14"><path d="M2 7h8M7 3l4 4-4 4" stroke="#e52b3a" stroke-width="2" fill="none"/></svg><b>Sydney</b> – 19 centres</span>
  <span><svg width="14" height="14"><path d="M2 7h8M7 3l4 4-4 4" stroke="#e52b3a" stroke-width="2" fill="none"/></svg><b>Brisbane</b> – 14 centres</span>
  <span><svg width="14" height="14"><path d="M2 7h8M7 3l4 4-4 4" stroke="#e52b3a" stroke-width="2" fill="none"/></svg><b>Adelaide</b> – 6 centres</span>
  <span><svg width="14" height="14"><path d="M2 7h8M7 3l4 4-4 4" stroke="#e52b3a" stroke-width="2" fill="none"/></svg><b>Cairns</b> – 1 centre</span>
  <span><svg width="14" height="14"><path d="M2 7h8M7 3l4 4-4 4" stroke="#e52b3a" stroke-width="2" fill="none"/></svg><b>Canberra</b> – 2 centres</span>
  <span><svg width="14" height="14"><path d="M2 7h8M7 3l4 4-4 4" stroke="#e52b3a" stroke-width="2" fill="none"/></svg><b>Wollongong</b> – 1 centre</span>
  <span><svg width="14" height="14"><path d="M2 7h8M7 3l4 4-4 4" stroke="#e52b3a" stroke-width="2" fill="none"/></svg><b>Gold Coast</b> – 5 centres</span>
  <span><svg width="14" height="14"><path d="M2 7h8M7 3l4 4-4 4" stroke="#e52b3a" stroke-width="2" fill="none"/></svg><b>Townsville</b> – 1 centre</span>
  <span><svg width="14" height="14"><path d="M2 7h8M7 3l4 4-4 4" stroke="#e52b3a" stroke-width="2" fill="none"/></svg><b>Melbourne</b> – 21 centres</span>
  <span><svg width="14" height="14"><path d="M2 7h8M7 3l4 4-4 4" stroke="#e52b3a" stroke-width="2" fill="none"/></svg><b>Central Coast</b> – 2 centres</span>
  <span><svg width="14" height="14"><path d="M2 7h8M7 3l4 4-4 4" stroke="#e52b3a" stroke-width="2" fill="none"/></svg><b>Sunshine Coast</b> – 2 centres</span>
  <span><svg width="14" height="14"><path d="M2 7h8M7 3l4 4-4 4" stroke="#e52b3a" stroke-width="2" fill="none"/></svg><b>Wodonga</b> – 1 centre</span>
  <span><svg width="14" height="14"><path d="M2 7h8M7 3l4 4-4 4" stroke="#e52b3a" stroke-width="2" fill="none"/></svg><b>Perth</b> – 11 centres</span>
</div>

<div class="ph ph-approach" role="img" aria-label="Photo of a young couple talking with a psychologist"></div>
<h2 class="sec" style="top:2510px;left:642px;width:460px;font-size:34px">Our Relationship <em>Counselling</em> Approach</h2>
<p class="body" style="top:2622px;left:642px;width:480px">It is an important part of our policy to take a very positive approach to our relationship counselling.<br><br>We feel it is important to really understand the problems and perspectives of each of you, and at the same time, we find that most couples are looking to find a positive action plan and way through their problems to make changes...</p>
<a class="btn" href="#" style="top:2789px;left:642px">Read More</a>

<h2 class="sec" style="top:2958px;left:78px;width:600px;font-size:34px">Communication is a vital skill but <em>not</em> often taught to us.</h2>
<p class="body" style="top:3065px;left:78px;width:600px">Most people find that their ways of communicating with each other are what hamper us from having a happy healthy relationship.<br><br>Effective Interpersonal Communication skills are not something that we are usually taught. But for almost everyone who is having difficulties in their relationship, they feel that they are trying to communicate their thoughts and feelings but that their partner is not listening...</p>
<a class="btn" href="#" style="top:3236px;left:78px">Read More</a>
<div class="ph ph-couple" role="img" aria-label="Photo of a couple embracing against a stone wall"></div>

<h2 class="sec" style="top:3390px;left:0;width:1200px;text-align:center;font-size:34px">FAQ's</h2>
<p class="body" style="top:3448px;left:0;width:1200px;text-align:center;font-size:17px;color:#555">Below is a list of frequently asked questions to help you understand how this works.</p>
<div class="faq-item" style="top:3500px">What happens in a marriage/relationship counselling session?</div>
<div class="faq-item open" style="top:3556px;border-bottom:0">What are the fees involved, and are there any rebates?</div>
<p class="body" style="top:3594px;left:100px;width:600px;color:#555">Private health rebates should apply. If you have 'psychology' as an extra, but we recommend that you call your fund and check your level of cover if this is of concern to you. Unfortunately funds don't give us these details.</p>
<a href="#" class="abs" style="top:3646px;left:610px;font-size:13px;font-weight:700;color:#2a5f7a;text-decoration:underline">READ MORE</a>
<div class="abs" style="top:3672px;left:78px;width:636px;height:2px;background:var(--teal-light)"></div>
<div class="faq-item" style="top:3700px;border-bottom:0">How helpful will it be?</div>
<div class="abs faq-vline"></div>
<h3 class="abs" style="top:3520px;left:770px;font-size:24px;font-weight:400;color:var(--red)">Questions?</h3>
<p class="body" style="top:3562px;left:770px;width:350px">Lorem Ipsum is simply dummy text of the printing and typesetting industry. Lorem Ipsum has been the industry's standard dummy text ever since the 1500s.</p>
<a class="btn" href="#" style="top:3660px;left:758px">Contact us to day</a>

<div class="abs blog-sec"></div>
<h2 class="sec" style="top:3870px;left:0;width:1200px;text-align:center;font-size:34px">Latest Blogs</h2>
<div class="blog b1" style="left:78px" role="img" aria-label="Blog photo of a couple in conversation"><span class="date">05 Apr, 2017</span><span class="t">Lorem Ipsum is simply dummy text.</span></div>
<div class="blog b2" style="left:444px" role="img" aria-label="Blog photo of a relaxed couple"><span class="date">05 Apr, 2017</span><span class="t">Lorem Ipsum is simply dummy text.</span></div>
<svg class="abs" style="top:4104px;left:581px" width="38" height="22" viewBox="0 0 38 22"><path d="M0 22 A19 19 0 0 1 38 22 Z" fill="#2a9d9b"/><path d="M19 9v10M14 14h10" stroke="#fff" stroke-width="2.5"/></svg>
<div class="blog b3" style="left:810px" role="img" aria-label="Blog photo of a couple outdoors"><span class="date">05 Apr, 2017</span><span class="t">Lorem Ipsum is simply dummy text.</span></div>

<div class="abs footer"></div>
<nav class="abs flinks"><a href="#">Privacy Policy</a><a href="#">Terms &amp; Conditions</a><a href="#">Site Map</a><a href="#">Associate Psychologists Program</a><a href="#">Contact Us</a></nav>
<div class="abs fbottom">
  <span class="c">© <u><b>The Kelvale Clinic</b></u> - 2017. All Rights Reserved.</span>
  <span class="s" style="left:1040px"></span><span class="s" style="left:1068px"></span><span class="s" style="left:1096px"></span>
</div>

</body>
</html>
```